Business card design needed

Family General Practitioner/ Family Physician.
Logo is the logo of the Noble Guild of Family Healers Oceania
http://kpltw.varendo.example/ImageShelf/marks/pages/NGFHO%20mark_jpg.htm
Updates

Project Deadline Extended
Reason: Just a bit more time to make changes and the weekend for me to look at things closely and to choose. Thanks, Orin

Thanks for all the submissions. So many of them are really works of art. Not one of them are not good. The ones that I am eliminating are the ones that I think are not suitable for me personally only, and because if I don't, it makes it very difficult to decide as many of you are also sending me slight variations of a card. I have just decided to choose a second place card too. Can't thank you all enough. Good luck, Orin. P.S - Working today till 10 pm as the card says :-), so probably won't be able to give a feedback till late Saturday night or Sunday morning here in Sydney, Australia. 

Project Deadline Extended
Reason: Just added a second place to the budget and realised that Australia is ahead of the rest of the world in the time zone (only :-) - don't want to offend anyone or start a debate!! ) , so Monday deadline will mean it will be a weekend for the rest of the world. Just wanted to give everyone more time to submit their best, especially since I will be picking a second card too. Can't thank everyone enough for the submissions. P.S - Not keen on photos on the card.

Industry/Entity Type

Business

Contact Information for Business Card

Dr. Orin Halvey M.B.B.S., F.N.G.F.H.O
Family General Practitioner
Address, timings, phone and fax number on the back.

Requirements
Must have
• Timings
Mon 7 am - 7 pm
Tues 7 am - 12 pm
Wed 7 am - 10 pm
Thurs 7 am - 12 pm
Fri 7 am - 8 pm
Sat 8 am - 10 pm
Sun - Off

```html
<!DOCTYPE html>
<html lang="en">
<head>
<meta charset="utf-8">
<title>Dr. Orin Halvey – Business Card</title>
<link rel="stylesheet" href="https://fonts.googleapis.com/css2?family=Open+Sans:wght@400;600;700&display=swap">
<style>
  :root {
    --backdrop: #1f2123;
    --card-cream: #ede3c6;
    --accent-green: #7e9a52;
    --ink-dark: #474343;
    --ink-body: #3d3935;
  }
  * { margin: 0; padding: 0; box-sizing: border-box; }
  html, body { width: 1200px; height: 395px; overflow: hidden; }
  body {
    background: var(--backdrop);
    font-family: "Open Sans", Arial, sans-serif;
    color: var(--ink-body);
    position: relative;
  }
  .card {
    position: absolute;
    top: 39px;
    width: 549px;
    height: 313px;
    background: var(--card-cream);
    overflow: hidden;
  }
  .card--front { left: 36px; }
  .card--back { left: 616px; }

  .pulse-line { position: absolute; left: 0; top: 0; }

  .guild-mark {
    position: absolute;
    left: 398px;
    top: 48px;
    width: 112px;
    height: 88px;
    background: var(--card-cream);
    display: flex;
    align-items: center;
    justify-content: center;
    gap: 6px;
  }
  .guild-mark__dot {
    width: 10px; height: 10px;
    border-radius: 50%;
    background: var(--accent-green);
    flex: none;
  }
  .guild-mark__name {
    font-size: 10px;
    font-weight: 600;
    line-height: 1.25;
    color: var(--ink-dark);
    text-align: left;
  }

  .doctor-name {
    position: absolute;
    left: 52px;
    top: 166px;
    font-size: 42px;
    font-weight: 700;
    color: var(--ink-dark);
    letter-spacing: -0.3px;
  }
  .credentials {
    position: absolute;
    left: 54px;
    top: 224px;
    font-size: 11px;
    color: var(--ink-body);
  }
  .role {
    position: absolute;
    left: 54px;
    top: 256px;
    font-size: 16.5px;
    color: var(--ink-body);
  }

  .contact {
    position: absolute;
    left: 0;
    width: 275px;
    top: 50px;
    text-align: center;
    font-size: 16px;
    line-height: 23px;
  }
  .contact b { font-weight: 700; }
  .address {
    position: absolute;
    left: 0;
    width: 275px;
    top: 213px;
    text-align: center;
    font-size: 16px;
    line-height: 22px;
  }

  .hours-panel {
    position: absolute;
    left: 275px;
    top: 0;
    width: 274px;
    height: 313px;
    background: var(--accent-green);
  }
  .hours-title {
    position: absolute;
    left: 0; width: 274px;
    top: 56px;
    text-align: center;
    font-size: 13.5px;
    font-weight: 700;
    text-decoration: underline;
    text-underline-offset: 3px;
  }
  .hours-table {
    position: absolute;
    left: 32px;
    top: 103px;
    border-collapse: collapse;
    font-size: 13.5px;
    font-weight: 700;
  }
  .hours-table td { padding: 0; height: 20px; line-height: 20px; }
  .hours-table .day { width: 102px; }
  .hours-table .sep { width: 20px; }
</style>
</head>
<body>
  <section class="card card--front">
    <svg class="pulse-line" width="549" height="313" viewBox="0 0 549 313" aria-hidden="true">
      <polyline fill="none" stroke="var(--accent-green)" stroke-width="4" stroke-linejoin="miter"
        points="0,88 50,88 56,67 61,88 84,88 88,71 93,107 107,23 118,141 130,61 136,88 140,65 146,88 549,88"/>
    </svg>
    <div class="guild-mark">
      <span class="guild-mark__dot"></span>
      <span class="guild-mark__name">Noble Guild of<br>Family Healers<br>Oceania</span>
    </div>
    <h1 class="doctor-name">Dr. Orin Halvey</h1>
    <p class="credentials">M.B.B.S., F.N.G.F.H.O</p>
    <p class="role">Family General Practitioner</p>
  </section>

  <section class="card card--back">
    <div class="contact">
      <p><b>P :</b> 02 7361 4580</p>
      <p><b>F :</b> 02 7361 4592</p>
    </div>
    <div class="address">
      <p>Upper Level, Lantern Court,</p>
      <p>willow crest shopping center</p>
      <p>ferngate, nsw 2199</p>
    </div>
    <div class="hours-panel">
      <h2 class="hours-title">WORKING HOURS</h2>
      <table class="hours-table">
        <tr><td class="day">Monday</td><td class="sep">:</td><td>7 AM -&nbsp; 7 PM</td></tr>
        <tr><td class="day">Tuesday</td><td class="sep">:</td><td>7 AM - 12 PM</td></tr>
        <tr><td class="day">Wednesday</td><td class="sep">:</td><td>7 AM - 10 PM</td></tr>
        <tr><td class="day">Thursday</td><td class="sep">:</td><td>7 AM - 12 PM</td></tr>
        <tr><td class="day">Friday</td><td class="sep">:</td><td>7 AM -&nbsp; 8 PM</td></tr>
        <tr><td class="day">Saturday</td><td class="sep">:</td><td>8 AM - 10 PM</td></tr>
        <tr><td class="day">Sunday</td><td class="sep">:</td><td>OFF</td></tr>
      </table>
    </div>
  </section>
</body>
</html>
```